New, modern business card for growing audiology practice

We need a new business card for our audiology practice. Our logo and website have recently changed (more modern) and we want our business cards to reflect this change.
We conduct hearing tests, perform earwax removals, and fit & dispense hearing aids to our patients. We are a family owned practice in which the owner is the one who works directly with the patient. I have attached logos in various formats to use, as well as two ideas I found on this website; as well as a scanned copy of our current logo. Good luck!

Industry/Entity Type

Business

Contact Information for Business Card

Company name: Tolvera Hearing Center
Provider name: Peter Wolstenby, Au.D. F/NSB
Phone number: (440) 683-5127
Address: 837 W. Lindell Ave. Marlow Falls, OH 44190
email: tolverahearing@postvane.com
website: tolverahearing.com

Colors
000000
aaaaaa
dbdbdb
cacaca
9bcb3c
afd23c
cadf82
b1b1b1

Requirements
Must have
• My card must include information in the "details" section. In the attached images, I found a few that I liked and I would like to model after - "brisky bouncin'" and "Sound Method Center".
• Must be horizontal.
• Must include logos provided. I uploaded them in various file formats and various ways.
• Must match logo font, if possible, if not, please get as close as you can.
Nice to have
• I really like the idea of having a color on one side with just the logo and company name and the contact information and provider name on the other side. I also really like the idea of having the main color dominating on the logo/company side with accent of that same color on the contact side of the card.
Should not have
• Must not be vertical.

```html
<!DOCTYPE html>
<html lang="en">
<head>
<meta charset="utf-8">
<title>Tolvera Hearing Center – Business Card</title>
<link rel="stylesheet" href="https://fonts.googleapis.com/css2?family=Jost:wght@400&family=Roboto:wght@400&family=Saira+Condensed:wght@600&display=swap">
<style>
  :root {
    --backdrop: #2e2e2e;
    --card: #1c1c1c;
    --card-edge: #262626;
    --ink-light: #f2f2f2;
    --ink-muted: #d6d6d6;
    --emboss: #4a4a4a;
    --green: #62a03a;
  }
  * { box-sizing: border-box; margin: 0; padding: 0; }
  html, body { width: 799px; height: 1200px; overflow: hidden; }
  body {
    background: var(--backdrop);
    display: flex;
    flex-direction: column;
    align-items: center;
    justify-content: center;
    gap: 120px;
  }
  .card {
    position: relative;
    width: 640px;
    height: 366px;
    background: var(--card);
    border: 1px solid var(--card-edge);
    border-radius: 4px;
    overflow: hidden;
  }
  .card--front {
    display: flex;
    align-items: center;
    justify-content: center;
  }
  .front-name {
    font-family: "Jost", sans-serif;
    font-weight: 400;
    font-size: 30px;
    letter-spacing: 2px;
    text-transform: uppercase;
    color: var(--emboss);
  }
  .back-brand {
    position: absolute;
    left: 40px;
    top: 38px;
    width: 250px;
    font-family: "Jost", sans-serif;
    font-weight: 400;
    font-size: 27px;
    line-height: 1.05;
    letter-spacing: 0.5px;
    text-transform: uppercase;
    color: var(--ink-light);
  }
  .provider {
    position: absolute;
    left: 40px;
    top: 140px;
  }
  .provider-name {
    font-family: "Saira Condensed", sans-serif;
    font-weight: 600;
    font-size: 22px;
    line-height: 1.1;
    color: var(--green);
  }
  .provider-role {
    font-family: "Roboto", sans-serif;
    font-size: 12px;
    color: var(--ink-muted);
    margin-top: 3px;
  }
  .contact {
    position: absolute;
    left: 40px;
    top: 208px;
    list-style: none;
    font-family: "Roboto", sans-serif;
    font-size: 15px;
    line-height: 19px;
    color: var(--ink-light);
  }
  .contact li { display: flex; align-items: flex-start; gap: 10px; }
  .contact .icon { width: 14px; height: 19px; flex: none; fill: var(--green); }
  .contact .no-icon { width: 14px; flex: none; }
  .accent-circle {
    position: absolute;
    right: -110px;
    top: 60px;
    width: 330px;
    height: 330px;
    border-radius: 50%;
    background: var(--green);
  }
</style>
</head>
<body>
  <section class="card card--front" aria-label="Card front">
    <p class="front-name">Tolvera Hearing Center</p>
  </section>

  <section class="card card--back" aria-label="Card back">
    <p class="back-brand">Tolvera Hearing Center</p>
    <div class="provider">
      <p class="provider-name">Peter Wolstenby, Au.D. F/NSB</p>
      <p class="provider-role">Owner - Audiologist</p>
    </div>
    <ul class="contact">
      <li>
        <svg class="icon" viewBox="0 0 14 19" aria-hidden="true"><path d="M7 2a5 5 0 0 0-5 5c0 3.8 5 9 5 9s5-5.2 5-9a5 5 0 0 0-5-5zm0 7a2 2 0 1 1 0-4 2 2 0 0 1 0 4z"/></svg>
        <span>837 W. Lindell Ave.</span>
      </li>
      <li><span class="no-icon"></span><span>Marlow Falls, OH 44190</span></li>
      <li>
        <svg class="icon" viewBox="0 0 14 19" aria-hidden="true"><path d="M3 4h3l1 3-2 1a8 8 0 0 0 3 3l1-2 3 1v3a1 1 0 0 1-1 1C6 14 2 10 2 5a1 1 0 0 1 1-1z"/></svg>
        <span>(440) 683-5127</span>
      </li>
      <li>
        <svg class="icon" viewBox="0 0 14 19" aria-hidden="true"><path d="M1 5h12v9H1zM1.8 5.8 7 10l5.2-4.2" stroke="#1c1c1c" stroke-width="1"/></svg>
        <span>tolverahearing@postvane.com</span>
      </li>
      <li>
        <svg class="icon" viewBox="0 0 14 19" aria-hidden="true"><circle cx="7" cy="9.5" r="5.5"/><path d="M1.5 9.5h11M7 4c-2 2-2 9 0 11M7 4c2 2 2 9 0 11" stroke="#1c1c1c" stroke-width="0.9" fill="none"/></svg>
        <span>www.tolverahearing.com</span>
      </li>
    </ul>
    <div class="accent-circle" aria-hidden="true"></div>
  </section>
</body>
</html>
```